Brightway Haus Inc. Business Card Design

Brightway Haus Inc. is in search of a great clean design for our business cards!

Looking to incorporate our full logo and watermark on side one (however, I am open to having the text and watermark separated within the design.)

On side two, I am looking to have contact information (Name, Position, Phone #, Email, Website (www.thebrightwayhaus.ca). Can have the logo and/or watermark as part of the design if applicable.

Please add tagline "Where Shine Counts" on either side 1 or 2. This tagline can be in a sans serif, serif or cursive font as long as it compliments overall design. Capitalization can be title or sentence case depending on how it fits within the design.

Get creative!! Looking for a clean, crisp, premium design! Looking for a glossy card finish with spot UV features when printed. Cards will also be printed with rounded corners. Standard dimensions (3.5 x 2).

Target Market(s)

B2B - primary clients are business owners or property management corporations. (residential jobs are few and far between)

Industry/Entity Type

Business

Contact Information for Business Card

- clean, crisp design
- double sided
- spot UV accents and glossy finish upon printing
- standard business card size (3.5 x 2) with rounded corners
- please see project description for requirements per side

Font styles to use
Sans Serif

Requirements
Must have
• - adequate bleeds with print ready files
• - cohesive design elements between side 1 & 2
• - spot UV elements (can be on both sides or just one, use your discretion)
• - colour pallet should match the logo file provided
• - incorporate tagline "where shine counts" (this tagline can be in a serif or sans serif font as long as it is complimentary to the overall design.
Nice to have
• - Premium elements with a clean design
Should not have
• - Please omit cartoon or whimsical like designs, think premium.
• - Colours should not stray from the pallet of the provided logo.

```html
<!DOCTYPE html>
<html lang="en">
<head>
<meta charset="utf-8">
<title>Brightway Haus Inc. Business Card</title>
<link rel="stylesheet" href="https://fonts.googleapis.com/css2?family=Open+Sans:wght@400;700&family=Roboto:wght@400;500&display=swap">
<style>
  :root {
    --backdrop: #3b3b3d;
    --card: #252527;
    --gloss: #3a3a3d;
    --teal: #00a9b0;
    --navy: #1c2150;
    --silver: #a4a7ab;
    --text-light: #e6e6e6;
  }
  * { margin: 0; padding: 0; box-sizing: border-box; }
  html, body { width: 799px; height: 1200px; overflow: hidden; }
  body {
    background: var(--backdrop);
    font-family: "Roboto", Arial, sans-serif;
    position: relative;
  }
  .card {
    position: absolute;
    left: 100px;
    width: 600px;
    height: 343px;
    border-radius: 16px;
    background: var(--card);
    overflow: hidden;
    box-shadow: 0 14px 30px rgba(0,0,0,0.45);
  }
  .card-front { top: 140px; }
  .card-back { top: 720px; }

  .front-mark {
    position: absolute;
    inset: 0;
    display: flex;
    align-items: center;
    justify-content: center;
    gap: 16px;
  }
  .front-mark .square {
    width: 44px; height: 44px;
    background: var(--gloss);
  }
  .front-mark .name {
    font-family: "Open Sans", Arial, sans-serif;
    font-weight: 700;
    font-size: 34px;
    color: var(--gloss);
    letter-spacing: 1px;
  }

  .brand {
    position: absolute;
    left: 34px; top: 30px;
  }
  .brand .name {
    font-family: "Open Sans", Arial, sans-serif;
    font-weight: 700;
    font-size: 30px;
    color: var(--teal);
    letter-spacing: -0.5px;
    line-height: 1;
  }
  .brand .tagline {
    font-family: "Open Sans", Arial, sans-serif;
    font-size: 13px;
    color: var(--silver);
    letter-spacing: 6px;
    margin-top: 4px;
  }
  .person {
    position: absolute;
    left: 34px; top: 112px;
  }
  .person .full-name {
    font-weight: 500;
    font-size: 24px;
    color: var(--teal);
  }
  .person .role {
    font-size: 13px;
    color: var(--text-light);
    margin-top: 2px;
  }
  .contact {
    position: absolute;
    left: 34px; top: 182px;
    font-size: 15px;
    color: var(--text-light);
    line-height: 22px;
    list-style: none;
  }
  .contact li { display: flex; align-items: center; gap: 8px; }
  .contact .address { padding-left: 22px; }
  .contact svg { width: 14px; height: 14px; fill: var(--teal); flex: none; }
  .contact .web-accent { color: var(--teal); }

  .accent-panel {
    position: absolute;
    right: 0; top: 110px;
    width: 200px; height: 233px;
  }
</style>
</head>
<body>
  <section class="card card-front" aria-label="Card front">
    <div class="front-mark">
      <span class="square"></span>
      <span class="name">Brightway Haus Inc.</span>
    </div>
  </section>

  <section class="card card-back" aria-label="Card back">
    <div class="brand">
      <div class="name">Brightway Haus Inc.</div>
      <div class="tagline">Where Shine Counts</div>
    </div>

    <div class="person">
      <div class="full-name">Daniel Reyes</div>
      <div class="role">Managing Director</div>
    </div>

    <ul class="contact">
      <li class="address">123, City Name</li>
      <li class="address">Street No, Country 123</li>
      <li>
        <svg viewBox="0 0 16 16"><path d="M3 1h3l1.5 4-2 1.2a9 9 0 0 0 4.3 4.3L11 8.5l4 1.5v3a2 2 0 0 1-2 2A12 12 0 0 1 1 3a2 2 0 0 1 2-2z"/></svg>
        1800-555-0142
      </li>
      <li>
        <svg viewBox="0 0 16 16"><path d="M1 3h14v10H1z M1 3l7 6 7-6" fill="none" stroke="#00a9b0" stroke-width="1.6"/></svg>
        danielreyes@yourweb.com
      </li>
      <li>
        <svg viewBox="0 0 16 16"><circle cx="8" cy="8" r="6.5" fill="none" stroke="#00a9b0" stroke-width="1.5"/><path d="M1.5 8h13M8 1.5c-3 3.5-3 9.5 0 13M8 1.5c3 3.5 3 9.5 0 13" fill="none" stroke="#00a9b0" stroke-width="1.2"/></svg>
        <span>www.<span class="web-accent">thebrightwayhaus</span>.ca</span>
      </li>
    </ul>

    <svg class="accent-panel" viewBox="0 0 200 233" aria-hidden="true">
      <rect x="0" y="0" width="200" height="170" fill="#00a9b0"/>
      <rect x="0" y="170" width="200" height="22" fill="#1c2150"/>
      <rect x="0" y="192" width="200" height="41" fill="#a4a7ab"/>
    </svg>
  </section>
</body>
</html>
```